Business card for builder specialising in renovations.

Need a card for our building business. Business name is under Martin Powles.
Have licence number on card ( 527691K)
Contact number (0400 382 415)
Want to work on logo for some business cards and shirts - something with MPB or MPB or open to ideas??
No animations, No hammers. Something sharp and eye catching.
Highlight that we are a renovation specialist. Simple on front with extra details on back with some lines to jot down things.

Target Market(s)

Renovators

Industry/Entity Type

Building

Contact Information for Business Card

2 sided with room on back to jot things down.
Extra details on back so front can be simple ..like, renovations, bathrooms, decks, extensions, new builds,

Logo Text

MPB

Font styles to use
Serif

Requirements
Must have
• Eye catching design .
• Name : Martin powles
• Licence number
• Contact number - 0400382415
Nice to have
• Some logo design that we can carry through to other forms of advertising
• Local builder
• Quality work
Should not have
• No animations

```html
<!DOCTYPE html>
<html lang="en">
<head>
<meta charset="utf-8">
<title>Martin Powles Building – Business Card</title>
<link rel="stylesheet" href="https://fonts.googleapis.com/css2?family=Open+Sans:wght@400;700&display=swap">
<style>
  :root {
    --backdrop: #4a3f3a;
    --card: #161616;
    --card-edge: #222;
    --brand-blue: #3d9ddc;
    --brand-grey: #bdbdbd;
    --ink-white: #f4f4f4;
  }
  * { box-sizing: border-box; margin: 0; padding: 0; }
  html, body { width: 1200px; height: 716px; overflow: hidden; }
  body {
    background: var(--backdrop);
    font-family: "Open Sans", Arial, sans-serif;
    position: relative;
  }
  .card {
    position: absolute;
    top: 78px;
    width: 340px;
    height: 560px;
    background: var(--card);
    border: 1px solid var(--card-edge);
    border-radius: 4px;
    box-shadow: 0 10px 30px rgba(0,0,0,0.35);
  }
  .card--services { left: 230px; }
  .card--contact { left: 630px; }

  .brand {
    position: absolute;
    top: 100px;
    left: 0;
    width: 100%;
    text-align: center;
    font-weight: 700;
    font-size: 60px;
    letter-spacing: 3px;
    color: var(--brand-grey);
    line-height: 1;
  }

  .services {
    position: absolute;
    top: 300px;
    right: 60px;
    list-style: none;
    text-align: right;
    color: var(--brand-blue);
    font-size: 19px;
    line-height: 1.5;
  }
  .services li:nth-child(2) { margin-right: 8px; }
  .services li:nth-child(3) { margin-right: 30px; }
  .services li:nth-child(4) { margin-right: 2px; }

  .contact {
    position: absolute;
    left: 44px;
    bottom: 58px;
    padding-left: 14px;
    border-left: 3px solid var(--brand-blue);
  }
  .contact__name {
    font-weight: 700;
    font-size: 25px;
    letter-spacing: 1px;
    text-transform: uppercase;
    line-height: 1.2;
  }
  .contact__first { color: var(--brand-blue); }
  .contact__last { color: var(--brand-grey); }
  .contact__phone {
    font-weight: 700;
    font-size: 27px;
    color: var(--ink-white);
    line-height: 1.2;
  }
  .contact__licence {
    font-size: 19px;
    color: var(--ink-white);
    margin-top: 4px;
  }
  .contact__rule {
    position: absolute;
    left: 0;
    bottom: -10px;
    width: 120px;
    height: 2px;
    background: var(--brand-blue);
  }
</style>
</head>
<body>
  <section class="card card--services" aria-label="Card back: services">
    <p class="brand">MPB</p>
    <ul class="services">
      <li>Renovation Specialist</li>
      <li>Bathrooms</li>
      <li>Decks</li>
      <li>Extensions</li>
      <li>New builds,</li>
    </ul>
  </section>

  <section class="card card--contact" aria-label="Card front: contact">
    <p class="brand">MPB</p>
    <div class="contact">
      <p class="contact__name"><span class="contact__first">Martin</span> <span class="contact__last">Powles</span></p>
      <p class="contact__phone">0400 382 415</p>
      <p class="contact__licence">Licence number 527691K</p>
      <span class="contact__rule"></span>
    </div>
  </section>
</body>
</html>
```